Business Card Design

We need a business card designed for our new company. Prefer a black card with white logo & writing.

Contact Information for Business Card

Ted Galloway, address: 7-4812 Fernhollow Road, Abbotsford, BC, V3K 8R2, Office Phone: 604-712-3390, Cell: 604-947-2164, Email: ted@resinworkshub.ca

Colors

Designer to choose only greyscale colors for use in the design.

```html
<!DOCTYPE html>
<html lang="en">
<head>
<meta charset="utf-8">
<title>Resinworks Hub – Business Card</title>
<link href="https://fonts.googleapis.com/css2?family=Montserrat:wght@400;700;800&display=swap" rel="stylesheet">
<style>
  :root {
    --stage: #1b1b1b;
    --card: #232323;
    --card-back: #202020;
    --ink: #ffffff;
    --ink-soft: #d9d9d9;
    --gloss: #0e0e0e;
    --ridge-light: #5a5a5a;
  }
  * { margin: 0; padding: 0; box-sizing: border-box; }
  html, body {
    width: 1200px; height: 1200px; overflow: hidden;
    background: var(--stage);
    font-family: "Montserrat", sans-serif;
  }
  .stage {
    width: 1200px; height: 1200px;
    display: flex; flex-direction: column;
    align-items: center; justify-content: center; gap: 56px;
  }
  .card {
    position: relative;
    width: 880px; height: 503px;
    box-shadow: 0 18px 40px rgba(0,0,0,.55);
    overflow: hidden;
  }
  .card--front { background: var(--card); color: var(--ink); }
  .card--back { background: var(--card-back); display: flex; align-items: center; justify-content: center; }

  .brand {
    position: absolute; left: 64px; top: 52px;
    display: flex; align-items: center; gap: 12px;
    font-weight: 800; font-size: 30px; letter-spacing: 1px;
    text-transform: uppercase; color: var(--ink);
  }
  .brand__dot { width: 14px; height: 14px; border-radius: 50%; background: var(--ink); }

  .person { position: absolute; left: 64px; top: 150px; }
  .person__name { font-weight: 700; font-size: 30px; letter-spacing: .5px; }
  .person__role { font-size: 17px; color: var(--ink-soft); margin-top: 2px; }

  .address {
    position: absolute; left: 64px; top: 238px;
    font-size: 18px; line-height: 1.3; color: var(--ink-soft);
    font-style: normal;
  }
  .contacts {
    position: absolute; left: 64px; top: 312px;
    list-style: none; font-size: 18px; color: var(--ink-soft);
  }
  .contacts li { display: flex; align-items: center; gap: 14px; height: 33px; }
  .contacts svg { width: 17px; height: 17px; fill: var(--ink); flex: none; }

  .ridge {
    position: absolute; right: 0; bottom: 0;
    width: 560px; height: 160px;
    background: linear-gradient(180deg, rgba(255,255,255,0) 0%, rgba(255,255,255,.05) 60%, rgba(255,255,255,.09) 100%);
  }

  .back-mark {
    display: flex; align-items: center; gap: 22px;
    font-weight: 800; font-size: 64px; letter-spacing: 2px;
    text-transform: uppercase; color: var(--gloss);
  }
  .back-mark__square { width: 40px; height: 40px; background: var(--gloss); }
</style>
</head>
<body>
<main class="stage">
  <section class="card card--front" aria-label="Business card front">
    <div class="brand"><span class="brand__dot"></span>Resinworks Hub</div>

    <div class="person">
      <h1 class="person__name">Ted Galloway</h1>
      <p class="person__role">owner</p>
    </div>

    <address class="address">7-4812 Fernhollow Road,<br>Abbotsford, BC, V3K 8R2</address>

    <ul class="contacts">
      <li>
        <svg viewBox="0 0 24 24" aria-hidden="true"><path d="M6.6 10.8a15.1 15.1 0 0 0 6.6 6.6l2.2-2.2a1 1 0 0 1 1-.25 11.4 11.4 0 0 0 3.6.57 1 1 0 0 1 1 1V20a1 1 0 0 1-1 1A17 17 0 0 1 3 4a1 1 0 0 1 1-1h3.5a1 1 0 0 1 1 1c0 1.25.2 2.45.57 3.57a1 1 0 0 1-.25 1z"/></svg>
        604-712-3390
      </li>
      <li>
        <svg viewBox="0 0 24 24" aria-hidden="true"><path d="M7 1h10a2 2 0 0 1 2 2v18a2 2 0 0 1-2 2H7a2 2 0 0 1-2-2V3a2 2 0 0 1 2-2zm0 3v14h10V4zm5 15.5a1.2 1.2 0 1 0 0 2.4 1.2 1.2 0 0 0 0-2.4z"/></svg>
        604-947-2164
      </li>
      <li>
        <svg viewBox="0 0 24 24" aria-hidden="true"><path d="M2 5h20v14H2zm2 2v.4l8 5.2 8-5.2V7zm0 2.8V17h16V9.8l-8 5.2z"/></svg>
        ted@resinworkshub.ca
      </li>
      <li>
        <svg viewBox="0 0 24 24" aria-hidden="true"><path d="M12 2a10 10 0 1 0 0 20 10 10 0 0 0 0-20zm6.9 6h-2.9a15.6 15.6 0 0 0-1.4-3.6A8 8 0 0 1 18.9 8zM12 4c.8 1.1 1.5 2.5 1.9 4h-3.8c.4-1.5 1.1-2.9 1.9-4zM4.3 14a8 8 0 0 1 0-4h3.4a16.5 16.5 0 0 0 0 4zm.8 2h2.9c.3 1.3.8 2.5 1.4 3.6A8 8 0 0 1 5.1 16zM8 8H5.1a8 8 0 0 1 4.3-3.6C8.8 5.5 8.3 6.7 8 8zm4 12c-.8-1.1-1.5-2.5-1.9-4h3.8c-.4 1.5-1.1 2.9-1.9 4zm2.3-6H9.7a14.7 14.7 0 0 1 0-4h4.6a14.7 14.7 0 0 1 0 4zm.3 5.6c.6-1.1 1.1-2.3 1.4-3.6h2.9a8 8 0 0 1-4.3 3.6zM16.3 14a16.5 16.5 0 0 0 0-4h3.4a8 8 0 0 1 0 4z"/></svg>
        www.resinworkshub.ca
      </li>
    </ul>

    <div class="ridge" role="img" aria-label="White line drawing of a mountain ridge along the lower right edge"></div>
  </section>

  <section class="card card--back" aria-label="Business card back">
    <div class="back-mark"><span class="back-mark__square"></span>Resinworks Hub</div>
  </section>
</main>
</body>
</html>
```